A website where experts collaborate on your project

I am building a new website where experts (yes, like designers) collaborate on projects with the project owner. More minds = more collaboration = better end product. Please see Pelmora(dot)com for a quick landing page I created for collaborating on presentations (although there will be many project types offered)

I am looking for a DESIGNER LONG TERM, but for now, just need initial mock ups to show the web programmers.

I have 21 Word documents loosely designed, what I would like to see here is a theme. Please DO NOT GO OFF WHAT YOU CURRENTLY SEE AT PELMORA. What is up now is only a quick landing page.

You can view a Word doc of the homepage here:
https://www.filevanta.com/s/qx83kdm2/home.docx?dl=0

WHAT AM I LOOKING FOR?
A clean, well designed theme.

Here is a link to the logo:
https://www.filevanta.com/s/mr47tpz9/logo%20-%20horizontal.tif?dl=0
-----------------------------------------
Here are a few sites I like the design of and what I like about them:
www.quenbrook.com-all around my favorite, beautiful graphics, clean layout, bold use of colors on a dark background
Ravelto.com- clean layout, The use of humans and bubble style elements.
Mintharbor.com :) clean, bold, unique pop art style but professional
plumevault.com - From the unique colors and artwork and the ability of that art to not interfere with the important elements of the site
sparkwidgets.com-clean, nice colors, well organized and separated sections.
www.dunmereco.com-love the font, use of colors and sectionalized style

All in all, I am not picky and open to so many styles. I would ultimately like the designer I pick to design all 21 pages.
Updates

Hello everyone,Moving forward, I would like you all to pay special attention to the section in my brief titled "Here are a few sites I like the design of and what I like about them". Please see below, I handpicked each one of these as sites I really like. Thank you.Here are a few sites I like the design of and what I like about them:Ravelto.com- clean layout, The use of humans and bubble style elements.Mintharbor.com :) clean, bold, unique pop art style but professionalwriteraccess.com - From the unique colors and artwork and the ability of that art to not interfere with the important elements of the sitegrowthgeeks.com-clean, nice colors, well organized and separated sections.www.dunmereco.com-love the font, use of colors and sectionalized stylewww.quenbrook.com-beautiful graphics, clean layout, bold use of colors----------------------------------------- Added Tuesday, November 24, 2015

I updated the homepage, you can see it here:https://www.dropbox.com/s/kwlkbsookq3cg2m/1new%20homepage.docx?dl=0I am modeling it after my favorite designed site: triplelift.comI love the dark colors with the orange glowing style boldness of the buttons. It's real clean too. Added Tuesday, November 24, 2015

Target Market(s)

small business owners, marketers, freelancer writers, graphic designers,

Industry/Entity Type

Building

Number of Pages Required

5+ page

Requirements
Must have
• I can't think of anything the project must have.
Nice to have
• WHAT AM I LOOKING FOR?
• A clean, well designed theme. I had a designer do a bit of work putting elements together, I found it to be very plain, but I like the Application Page (https://www.filevanta.com/s/jb19ckr3/Pelmora-Website.ai?dl=0)
• Here is a link to the logo:
• https://www.filevanta.com/s/mr47tpz9/logo%20-%20horizontal.tif?dl=0
• Here are a few sites I like the design of and what I like about them:
• Ravelto.com- clean layout, The use of humans and bubble style elements.
• Mintharbor.com :) clean, bold, unique pop art style but professional
• plumevault.com - From the unique colors and artwork and the ability of that art to not interfere with the important elements of the site
• sparkwidgets.com-clean, nice colors, well organized and separated sections.
• www.dunmereco.com-love the font, use of colors and sectionalized style
• www.quenbrook.com-beautiful graphics, clean layout, bold use of colors
• -----------------------------------------
Should not have
• out of the boxed, templated style website. I want this site to be memorable and not look like a thousand others

```html
<!DOCTYPE html>
<html lang="en">
<head>
<meta charset="utf-8">
<title>Pelmora – Experts collaborating on your project</title>
<link href="https://fonts.googleapis.com/css2?family=Open+Sans:ital,wght@0,300;0,400;0,600;0,700;1,400&family=Raleway:wght@600;700&display=swap" rel="stylesheet">
<style>
:root{
  --orange:#f0901f;
  --orange-dark:#e27d12;
  --teal:#4fa3b8;
  --teal-text:#3e9fc0;
  --ink:#333;
  --muted:#666;
  --line:#e6e6e6;
  --soft:#f5f5f5;
  --white:#fff;
}
*{box-sizing:border-box;margin:0;padding:0}
html,body{width:912px;height:1200px;overflow:hidden}
body{font-family:"Open Sans",Arial,sans-serif;color:var(--ink);background:var(--white);position:relative}
.abs{position:absolute}

/* header */
.brand{left:76px;top:24px;display:flex;align-items:center;gap:8px}
.brand-name{font-size:22px;font-weight:700;color:var(--orange);letter-spacing:-.3px}
.brand-dot{width:50px;height:50px;border-radius:50%;background:var(--orange)}
.notice{left:393px;top:37px;width:380px;font-size:8.6px;line-height:15.5px;color:var(--teal-text)}
.notice b{font-weight:400;color:var(--orange)}

/* nav */
.navbar{left:0;top:94px;width:912px;height:38px;background:linear-gradient(var(--orange),var(--orange-dark))}
.browse{left:76px;top:100px;width:203px;height:24px;border:1px solid #fff;border-radius:2px;background:var(--orange-dark);color:#fff;font-size:9.5px;line-height:22px;padding-left:9px}
.browse span{position:absolute;right:0;top:0;width:30px;height:22px;border-left:1px solid rgba(255,255,255,.5);text-align:center;font-size:8px}
.nav{left:341px;top:94px;display:flex;height:38px}
.nav a{display:block;height:38px;line-height:38px;color:#fff;font-size:9.6px;text-decoration:none;text-align:center;border-right:1px solid rgba(0,0,0,.06)}
.nav a.active{background:var(--teal)}

/* hero */
.hero{left:0;top:132px;width:912px;height:356px;background:linear-gradient(100deg,#3c4656 0%,#6e7886 30%,#9aa3ad 50%,#6b7482 75%,#2e3440 100%)}
.hero-title{left:76px;top:246px;font-size:29px;font-weight:700;color:#fff}
.hero-sub{left:77px;top:280px;font-size:15.5px;font-weight:300;color:#fff;line-height:23px;width:340px}
.hero-btn{left:76px;top:333px;width:107px;height:32px;background:var(--orange);color:#fff;font-size:9.5px;text-align:center;line-height:32px;border-radius:2px}
.arrow{top:279px;width:27px;height:27px;border-radius:50%;background:rgba(0,0,0,.45);border:1px solid rgba(255,255,255,.2)}
.arrow svg{display:block;margin:7px auto}

/* panels */
.panel{border:1px solid #e2e2e2;background:#fff}
.panel-head{height:34px;background:linear-gradient(var(--orange),var(--orange-dark));color:#fff;font-size:14px;font-weight:300;line-height:34px;padding-left:17px;position:relative}
.filters{left:75px;top:519px;width:217px;height:324px}
.slider{position:relative;height:58px;border-bottom:1px solid var(--line)}
.track{position:absolute;left:24px;top:23px;width:158px;height:3px;background:#e9e9e9}
.track i{position:absolute;left:0;top:0;width:79px;height:3px;background:var(--teal)}
.knob{position:absolute;top:18px;width:12px;height:12px;border-radius:50%;background:var(--teal);border:2px solid #d3e9ef}
.range{position:absolute;top:40px;font-size:9px;color:var(--muted)}
.filter-row{height:27.3px;border-bottom:1px solid var(--line);position:relative;font-size:9.4px;color:#444;line-height:27px;padding-left:52px}
.filter-row .ico{position:absolute;left:21px;top:9px;width:9px;height:9px;background:#555;border-radius:2px}
.filter-row .ico.round{border-radius:50%}
.filter-row .chev{position:absolute;right:26px;top:0;color:#777;font-size:10px}
.save{position:absolute;left:-1px;bottom:-1px;width:217px;height:25px;background:var(--teal);color:#fff;font-size:11px;text-align:center;line-height:25px}

.projects{left:313px;top:519px;width:520px;height:324px}
.sort{position:absolute;right:26px;top:0;font-size:9px}
.sort u{text-decoration:underline}
.project{position:absolute;left:0;width:509px;border-bottom:1px solid #eee}
.project.alt{background:#f7f7f7}
.avatar{position:absolute;left:21px;width:57px;height:57px;border-radius:50%;background:linear-gradient(#dfe3e8,#9aa4b0);border:1px solid #ddd}
.p-text{position:absolute;left:103px;font-size:8.6px;color:#444}
.p-meta{position:absolute;left:103px;font-size:9.8px;color:#444}
.p-meta b{color:var(--teal-text);font-weight:600;margin-right:10px}
.view{position:absolute;left:392px;width:81px;height:28px;border:1px solid var(--teal);color:var(--teal-text);font-size:9.4px;text-align:center;line-height:26px;border-radius:2px}
.scroll{position:absolute;right:0;top:34px;width:10px;height:289px;background:#f3f3f3;border-left:1px solid #ddd}
.scroll i{position:absolute;left:1px;top:45px;width:7px;height:28px;background:#e0e0e0;border:1px solid #bbb}

/* testimonials */
.testi{left:0;top:881px;width:912px;height:248px;background:var(--soft);border-top:1px solid #e8e8e8}
.testi h2{position:absolute;left:0;width:912px;top:39px;text-align:center;font-family:"Raleway",sans-serif;font-size:24px;font-weight:700;color:#333}
.bubble{left:137px;top:959px;width:110px;height:98px;border-radius:50%;background:linear-gradient(#eef0f2,#b5bcc4);border:1px solid #ddd}
.quote{left:341px;top:970px;width:418px;font-size:9.4px;font-style:italic;line-height:18.4px;color:#666}
.qmark{font-family:Georgia,serif;font-size:26px;color:#c9c9c9}
.who{left:341px;top:1068px;font-size:9.6px;font-weight:700;color:var(--orange)}
.role{left:341px;top:1085px;font-size:8.6px;color:#333}
.dots{left:767px;top:1062px;display:flex;gap:3px}
.dots i{width:9px;height:9px;border-radius:50%;background:#bbb}

/* footer */
.footer{left:0;top:1129px;width:912px;height:71px;background:linear-gradient(var(--orange),var(--orange-dark))}
.f-links{left:76px;top:1146px;font-size:9.6px;color:#fff;word-spacing:2px}
.f-copy{left:74px;top:1166px;font-size:9.6px;color:#fff}
.social{left:682px;top:1154px;display:flex;gap:8px}
.social i{width:25px;height:25px;border-radius:50%;background:rgba(255,255,255,.85)}
</style>
</head>
<body>

<div class="abs brand"><span class="brand-name">pelmora</span><span class="brand-dot"></span></div>
<p class="abs notice"><b>Notification feed-New items</b> in the feeds are highlighted in blue,and they stay highlighted until cleared.&nbsp; You can clear highlights individually or clear them all at once.</p>

<div class="abs navbar"></div>
<div class="abs browse">Browse<span>&#8964;</span></div>
<nav class="abs nav">
  <a class="active" style="width:86px">Home</a>
  <a style="width:104px">Projects</a>
  <a style="width:111px">How it works</a>
  <a style="width:85px">Plans</a>
  <a style="width:109px">My Account</a>
</nav>

<div class="abs hero" role="img" aria-label="Photo of business people collaborating around a meeting table"></div>
<h1 class="abs hero-title">Convert more customers</h1>
<p class="abs hero-sub">Experience the power of experts collaborating on your project.</p>
<div class="abs hero-btn">Get Started</div>
<div class="abs arrow" style="left:28px"><svg width="10" height="12" viewBox="0 0 10 12"><path d="M7 1L2 6l5 5" stroke="#fff" stroke-width="1.6" fill="none"/></svg></div>
<div class="abs arrow" style="left:860px"><svg width="10" height="12" viewBox="0 0 10 12"><path d="M3 1l5 5-5 5" stroke="#fff" stroke-width="1.6" fill="none"/></svg></div>

<section class="abs panel filters">
  <div class="panel-head">Filters
    <svg style="position:absolute;right:16px;top:12px" width="10" height="10" viewBox="0 0 10 10"><path d="M0 0h10L6 5v5L4 8V5z" fill="#fff"/></svg>
  </div>
  <div class="slider">
    <div class="track"><i></i></div>
    <span class="knob" style="left:19px"></span>
    <span class="knob" style="left:97px"></span>
    <span class="range" style="left:20px">$20</span>
    <span class="range" style="left:174px">$1000</span>
  </div>
  <div class="filter-row"><i class="ico round"></i>Country<span class="chev">&#8250;</span></div>
  <div class="filter-row"><i class="ico"></i>Categories<span class="chev">&#8250;</span></div>
  <div class="filter-row"><i class="ico round"></i>Time Left<span class="chev">&#8250;</span></div>
  <div class="filter-row"><i class="ico"></i>Active | Expired<span class="chev">&#8250;</span></div>
  <div class="filter-row"><i class="ico"></i>Contains adult content<span class="chev">&#8250;</span></div>
  <div class="filter-row"><i class="ico"></i>keywords<span class="chev">&#8250;</span></div>
  <div class="filter-row" style="border-bottom:0"><i class="ico round"></i>followers<span class="chev">&#8250;</span></div>
  <div class="save">Save Filters</div>
</section>

<section class="abs panel projects">
  <div class="panel-head">Crowd Projects<span class="sort">Sort: &nbsp;<u>Price</u> &nbsp;|&nbsp; Country &nbsp;|&nbsp; Time left</span></div>
  <div class="project" style="top:34px;height:92px">
    <div class="avatar" style="top:20px" role="img" aria-label="Expert profile photo"></div>
    <p class="p-text" style="top:37px">Morbi in ante arcu. Maecenas sit amet sem vel</p>
    <p class="p-meta" style="top:54px"><b>$80</b>U.S time 6days</p>
    <div class="view" style="top:31px">View more</div>
  </div>
  <div class="project alt" style="top:126px;height:90px">
    <div class="avatar" style="top:17px" role="img" aria-label="Expert profile photo"></div>
    <p class="p-text" style="top:34px">Lorem ipsum dolor sit amet, consectetur adipiscing</p>
    <p class="p-meta" style="top:51px"><b>$80</b>U.S time 6days</p>
    <div class="view" style="top:27px">View more</div>
  </div>
  <div class="project" style="top:216px;height:107px;border-bottom:0">
    <div class="avatar" style="top:27px" role="img" aria-label="Expert profile photo"></div>
    <p class="p-text" style="top:45px">Morbi in ante arcu. Maecenas sit amet sem vel</p>
    <p class="p-meta" style="top:61px"><b>$80</b>U.S time 6days</p>
    <div class="view" style="top:37px">View more</div>
  </div>
  <div class="scroll"><i></i></div>
</section>

<section class="abs testi"><h2>Testimonials</h2></section>
<div class="abs bubble" role="img" aria-label="Portrait of the client giving the testimonial"></div>
<span class="abs qmark" style="left:315px;top:955px">&ldquo;</span>
<span class="abs qmark" style="left:778px;top:1004px">&rdquo;</span>
<p class="abs quote">With Pelmora I have multiple experts perfecting my content and I only pay for the feedback I find valuable. It’s perfect” Dale Ferrin, CEO, Northgate 9| “Before you put any content in front of your audience, crowdsource it with Pelmora, you won’t regret it” Owen Hartley, CEO, Lumenrow | “Pelmora is the best kept secret on the internet for converting more prospects to customers. I don’t know where my business would be today without it</p>
<p class="abs who">OWEN HARTLEY</p>
<p class="abs role">CEO, Lumenrow</p>
<div class="abs dots"><i></i><i></i></div>

<footer class="abs footer"></footer>
<p class="abs f-links">Home &nbsp;/ &nbsp; Projects &nbsp;/ &nbsp; How it works &nbsp;/ &nbsp; Plans &nbsp;/ &nbsp; My Account</p>
<p class="abs f-copy">Copyright © 2015 pelmora – All Rights Reserved</p>
<div class="abs social"><i></i><i></i><i></i><i></i><i></i></div>

</body>
</html>
```